Harborview Estates Business Card for Apartment Buildings

Create business cards for resident managers who run apartment buildings. The audience is the public who are searching for apartment rentals, and current residents who live at the apartment building. Key design element will be incorporating the company logo, however, the logo cannot dominate. The building name and manager name are more important than the logo. Current business card design leaves little room for copy, so we may need to reduce the size on the current card to allow for more space for copy.

Target Market(s)

Adults 18-65 years of age, who are looking for an apartment rental, plus current residents who live at our apartment buildings.

Industry/Entity Type

Property Management

Contact Information for Business Card

A major design element will be use of the company logo. Important property and manager contact information must be part of the design. The size of the logo will need to be reduced to make room for building and manager contact copy.

Font styles to use
Sans Serif

Colors
3176b5
000000
959595
ffffff

Requirements
Must have
• 1) Incorporate the company logo.
• 2) Use the company colors (dark blue, black/grey, over white).
• 3) FEATURE THE BUILDING NAME
• 4) FEATURE THE MANAGER NAME
• 5) The company name is less important than BUILDING and MANAGER
• 6) Manager contact information
• **SEE ATTACHED CREATIVE BRIEF**
Nice to have
• 1) Back of card logo watermark
• 2) Ability to write notes on back of carfd
Should not have
• Avoid letting the company logo dominate the card, the building name and manager are more important than the company logo.

```html
<!DOCTYPE html>
<html lang="en">
<head>
<meta charset="utf-8">
<title>Harborview Estates – Resident Manager Business Card</title>
<link rel="stylesheet" href="https://fonts.googleapis.com/css2?family=Catamaran:wght@400;500;600;700&family=Arimo:wght@400;700&display=swap">
<style>
  :root {
    --brand-blue: #1f6fb2;
    --ink-grey: #5a5a5a;
    --rule-grey: #8a8a8a;
    --band-dark: #3c3d40;
    --card-light: #e6e7e7;
    --card-dark: #3a3b3f;
    --mark-dark: #55565b;
    --stage: #a2a2a2;
    --white: #ffffff;
  }
  * { box-sizing: border-box; margin: 0; padding: 0; }
  html, body {
    width: 1200px; height: 1200px; overflow: hidden;
    background: var(--stage);
  }
  .sheet { position: relative; width: 1200px; height: 1200px; }
  .card {
    position: absolute; left: 205px; width: 790px; height: 451px;
    border-radius: 24px; overflow: hidden;
    font-family: "Catamaran", "Helvetica Neue", Arial, sans-serif;
  }
  .card-front { top: 92px; background: var(--card-light); }
  .card-back { top: 657px; background: var(--card-dark); }

  /* front */
  .brand {
    position: absolute; top: 64px; right: 43px;
    display: flex; align-items: center; gap: 14px;
  }
  .brand-square { width: 34px; height: 34px; background: var(--brand-blue); }
  .brand-name {
    font-size: 36px; font-weight: 700; color: var(--brand-blue);
    letter-spacing: 0.5px; line-height: 1;
  }
  .manager { position: absolute; left: 43px; top: 190px; }
  .manager-name {
    font-size: 28px; font-weight: 700; color: var(--brand-blue); line-height: 1.1;
  }
  .manager-title {
    margin-top: 6px; font-size: 17px; font-weight: 400; color: var(--ink-grey);
  }
  .divider {
    position: absolute; left: 43px; right: 43px; top: 271px;
    height: 2px; background: var(--rule-grey);
  }
  .contact-list {
    position: absolute; left: 43px; top: 284px; list-style: none;
  }
  .contact-list li {
    display: flex; align-items: center; gap: 10px;
    height: 28px; font-size: 17px; color: var(--ink-grey);
  }
  .contact-list svg { width: 16px; height: 16px; fill: var(--brand-blue); flex: none; }
  .property {
    position: absolute; right: 43px; top: 310px; text-align: right;
    font-size: 17px; line-height: 28px; color: var(--ink-grey);
  }
  .property-name { color: var(--brand-blue); font-weight: 500; }
  .footer-band { position: absolute; left: 0; bottom: 0; width: 790px; height: 42px; }
  .footer-label {
    position: absolute; right: 43px; bottom: 8px;
    font-size: 15px; font-weight: 700; letter-spacing: 0.6px;
    color: var(--white); text-transform: uppercase;
  }

  /* back */
  .back-brand {
    position: absolute; left: 0; right: 0; top: 200px;
    display: flex; justify-content: center; align-items: center; gap: 18px;
  }
  .back-brand .brand-square { width: 50px; height: 50px; background: var(--mark-dark); }
  .back-brand .brand-name { font-size: 54px; color: var(--mark-dark); }
  .website {
    position: absolute; left: 0; right: 0; top: 398px; text-align: center;
    font-family: "Arimo", Arial, sans-serif; font-size: 17px; letter-spacing: 1.2px;
    color: var(--white);
  }
  .website .accent { color: var(--brand-blue); }
</style>
</head>
<body>
<main class="sheet">

  <section class="card card-front" aria-label="Business card front">
    <div class="brand">
      <span class="brand-square"></span>
      <span class="brand-name">Harborview Estates</span>
    </div>

    <div class="manager">
      <h1 class="manager-name">Marisol Delgado</h1>
      <p class="manager-title">Resident Manager</p>
    </div>

    <div class="divider"></div>

    <ul class="contact-list">
      <li>
        <svg viewBox="0 0 24 24" aria-hidden="true"><path d="M6.6 10.8a15.1 15.1 0 0 0 6.6 6.6l2.2-2.2c.3-.3.7-.4 1-.2 1.1.4 2.3.6 3.6.6.6 0 1 .4 1 1V20c0 .6-.4 1-1 1A17 17 0 0 1 3 4c0-.6.4-1 1-1h3.5c.6 0 1 .4 1 1 0 1.3.2 2.5.6 3.6.1.3 0 .7-.2 1z"/></svg>
        555-214-3080
      </li>
      <li>
        <svg viewBox="0 0 24 24" aria-hidden="true"><path d="M6 2h12v5H6zM4 8h16a2 2 0 0 1 2 2v7h-4v5H6v-5H2v-7a2 2 0 0 1 2-2zm4 8v4h8v-4z"/></svg>
        555-214-3081
      </li>
      <li>
        <svg viewBox="0 0 24 24" aria-hidden="true"><path d="M7 1h10a2 2 0 0 1 2 2v18a2 2 0 0 1-2 2H7a2 2 0 0 1-2-2V3a2 2 0 0 1 2-2zm0 3v14h10V4zm5 15.5a1.2 1.2 0 1 0 0 2.4 1.2 1.2 0 0 0 0-2.4z"/></svg>
        555-806-4417
      </li>
      <li>
        <svg viewBox="0 0 24 24" aria-hidden="true"><path d="M2 5h20v14H2zm2 2v.4l8 5.3 8-5.3V7zm0 2.8V17h16V9.8l-8 5.3z"/></svg>
        marisol@harborviewest.com
      </li>
    </ul>

    <address class="property">
      <div class="property-name">Linden Court Apartments</div>
      <div>2485 Maple Avenue</div>
      <div>Crestmont, CA 92180</div>
    </address>

    <svg class="footer-band" viewBox="0 0 790 42" preserveAspectRatio="none" aria-hidden="true">
      <path d="M0 24 H430 C470 24 480 10 525 10 H790 V42 H0 Z" fill="var(--brand-blue)"/>
      <path d="M0 17 H440 C470 17 482 6 520 5" fill="none" stroke="var(--band-dark)" stroke-width="6"/>
    </svg>
    <span class="footer-label">Linden Court Apartments</span>
  </section>

  <section class="card card-back" aria-label="Business card back">
    <div class="back-brand">
      <span class="brand-square"></span>
      <span class="brand-name">Harborview Estates</span>
    </div>
    <p class="website"><span class="accent">www.</span>harborviewestates<span class="accent">.us</span></p>
  </section>

</main>
</body>
</html>
```